New Business Card Design Project

Need a design that will create an impact / strong impression towards our clients for our business. We are in the lighting business and we do lighting retrofits for large commercial to industrial clientele.

Target Market(s)

Lighting Industry

Industry/Entity Type

Business

Font styles to use
Other font styles liked:
• we would like to use the font on our logo, not sure what it is though..

Requirements
Must have
• Our logo.
Nice to have
• We are open to suggestions that have to do with lighting.

```html
<!DOCTYPE html>
<html lang="en">
<head>
<meta charset="utf-8">
<title>Northline Relamping Co. — Business Card</title>
<link href="https://fonts.googleapis.com/css2?family=Roboto:ital,wght@0,400;0,500;0,700;1,700&family=Roboto+Condensed:wght@500;700&display=swap" rel="stylesheet">
<style>
  :root {
    --backdrop: #2b2b2b;
    --forest: #133d12;
    --deep-green: #0f3a10;
    --leaf-green: #5cc24f;
    --title-green: #1b9a3f;
    --paper: #f1f1f1;
    --ink: #4a4a4a;
    --rule: #c9c9c9;
    --white: #ffffff;
  }
  html, body {
    margin: 0;
    padding: 0;
    width: 1200px;
    height: 960px;
    overflow: hidden;
    background: var(--backdrop);
    font-family: "Roboto", Arial, sans-serif;
  }
  .stage {
    position: relative;
    width: 1200px;
    height: 960px;
  }
  .card {
    position: absolute;
    left: 320px;
    width: 600px;
    height: 342px;
    border-radius: 20px;
    overflow: hidden;
  }
  /* Back side */
  .card-back {
    top: 108px;
    background: var(--forest);
  }
  .card-back .brand-name {
    position: absolute;
    left: 0;
    right: 0;
    top: 136px;
    color: var(--white);
    font-family: "Roboto Condensed", Arial, sans-serif;
    font-weight: 700;
    font-size: 40px;
    line-height: 48px;
    letter-spacing: 1px;
    white-space: nowrap;
    display: flex;
    justify-content: center;
    align-items: center;
    gap: 14px;
  }
  .card-back .brand-square {
    width: 22px;
    height: 22px;
    background: var(--white);
  }
  .card-back .website {
    position: absolute;
    left: 0;
    right: 0;
    top: 280px;
    text-align: center;
    color: var(--white);
    font-size: 14px;
    letter-spacing: 2.6px;
  }
  /* Front side */
  .card-front {
    top: 493px;
    background: var(--paper);
  }
  .card-front .brand-name {
    position: absolute;
    left: 36px;
    top: 134px;
    width: 290px;
    color: var(--deep-green);
    font-family: "Roboto Condensed", Arial, sans-serif;
    font-weight: 700;
    font-size: 23px;
    line-height: 28px;
    white-space: nowrap;
    display: flex;
    align-items: center;
    justify-content: center;
    gap: 10px;
  }
  .card-front .brand-square {
    width: 16px;
    height: 16px;
    background: var(--leaf-green);
    flex: none;
  }
  .divider {
    position: absolute;
    left: 338px;
    top: 58px;
    width: 1px;
    height: 190px;
    background: linear-gradient(to bottom, transparent, var(--rule) 20%, var(--rule) 80%, transparent);
  }
  .contact {
    position: absolute;
    left: 371px;
    top: 60px;
  }
  .person-name {
    margin: 0;
    font-family: "Roboto Condensed", Arial, sans-serif;
    font-weight: 700;
    font-size: 23px;
    line-height: 28px;
    color: var(--deep-green);
  }
  .person-title {
    margin: 0;
    font-family: "Roboto", Arial, sans-serif;
    font-weight: 500;
    font-size: 15px;
    line-height: 20px;
    color: var(--title-green);
  }
  .address {
    margin: 10px 0 10px;
    font-size: 15px;
    line-height: 18px;
    color: var(--ink);
  }
  .contact-list {
    list-style: none;
    margin: 0;
    padding: 0;
    font-size: 15px;
    line-height: 19px;
    color: var(--ink);
  }
  .contact-list li {
    display: flex;
    align-items: center;
    gap: 8px;
  }
  .contact-list svg {
    width: 14px;
    height: 14px;
    fill: var(--deep-green);
    flex: none;
  }
  .footer-rule {
    position: absolute;
    left: 0;
    bottom: 40px;
    width: 600px;
    height: 3px;
    background: var(--leaf-green);
  }
  .footer-band {
    position: absolute;
    left: 0;
    bottom: 0;
    width: 600px;
    height: 38px;
    background: var(--deep-green);
  }
  .footer-website {
    position: absolute;
    right: 22px;
    bottom: 11px;
    color: var(--white);
    font-weight: 700;
    font-style: italic;
    font-size: 14px;
  }
</style>
</head>
<body>
<main class="stage">

  <section class="card card-back" aria-label="Card back">
    <div class="brand-name"><span class="brand-square"></span>Northline Relamping Co.</div>
    <div class="website">www.northlinerelamping.com</div>
  </section>

  <section class="card card-front" aria-label="Card front">
    <div class="brand-name"><span class="brand-square"></span>Northline Relamping Co.</div>
    <div class="divider"></div>

    <div class="contact">
      <p class="person-name">DANIEL REYES</p>
      <p class="person-title">CEO/FOUNDER</p>
      <p class="address">2140 Birchwood Avenue<br>Fairbanks, Alaska 99701</p>
      <ul class="contact-list">
        <li>
          <svg viewBox="0 0 16 16" aria-hidden="true"><path d="M3.6 1.2l2.4 2.6-1.3 1.9c.9 2 2.6 3.7 4.6 4.6l1.9-1.3 2.6 2.4-1.4 2.6C7 13.6 2.4 9 1 3.6z"/></svg>
          555 210 4471
        </li>
        <li>
          <svg viewBox="0 0 16 16" aria-hidden="true"><path d="M4.5 1h7a1 1 0 0 1 1 1v12a1 1 0 0 1-1 1h-7a1 1 0 0 1-1-1V2a1 1 0 0 1 1-1zm.6 2v8.5h5.8V3zM8 12.3a.9.9 0 1 0 0 1.8.9.9 0 0 0 0-1.8z"/></svg>
          555 389 1206
        </li>
        <li>
          <svg viewBox="0 0 16 16" aria-hidden="true"><path d="M4 1h8v4H4zM2 6h12a1 1 0 0 1 1 1v5h-3v3H4v-3H1V7a1 1 0 0 1 1-1zm3.2 5v2.8h5.6V11z"/></svg>
          555 742 0583
        </li>
        <li>
          <svg viewBox="0 0 16 16" aria-hidden="true"><path d="M1 4h14v9H1zm1.4 1L8 9l5.6-4z"/></svg>
          daniel@northlinemail.com
        </li>
      </ul>
    </div>

    <div class="footer-rule"></div>
    <div class="footer-band"></div>
    <div class="footer-website">www.northlinerelamping.com</div>
  </section>

</main>
</body>
</html>
```